Health Care Company with Logo Needs Business Cards designed

We are a luxury behavioral health company looking for business cards design we already have a logo and are looking for someone to design a sophisticated luxurious looking business card. Please note that Card design should be captivating just like the logo and also encompass the logo color

Industry/Entity Type

Healthcare

Contact Information for Business Card

Logo,company name, tagline, my name and title, contact details, and physical address

```html
<!DOCTYPE html>
<html lang="en">
<head>
<meta charset="utf-8">
<title>Elvane Behavioral Health — Business Card</title>
<link href="https://fonts.googleapis.com/css2?family=Oswald:wght@500&family=Roboto:wght@400;500&family=Roboto+Condensed:wght@700&display=swap" rel="stylesheet">
<style>
  :root {
    --backdrop: #e4e4e4;
    --blue: #1b97de;
    --indigo: #4d66bd;
    --purple: #7e3b98;
    --cyan: #12a7e4;
    --ink: #1f1f1f;
    --white: #ffffff;
  }
  * { margin: 0; padding: 0; box-sizing: border-box; }
  html, body {
    width: 1200px;
    height: 900px;
    overflow: hidden;
    background: var(--backdrop);
  }
  .stage { position: relative; width: 1200px; height: 900px; }

  .card {
    position: absolute;
    top: 217px;
    width: 309px;
    height: 500px;
    overflow: hidden;
    box-shadow: 2px 3px 6px rgba(0,0,0,0.25);
  }

  /* Front: gradient side */
  .card--front {
    left: 279px;
    border-radius: 0 62px 0 62px;
    background: linear-gradient(200deg, var(--blue) 0%, var(--indigo) 45%, var(--purple) 85%);
    color: var(--white);
    text-align: center;
  }
  .card--front .backdrop-shape {
    position: absolute;
    left: 70px;
    top: 20px;
    width: 420px;
    height: 420px;
    border-radius: 50%;
    background: var(--white);
    opacity: 0.07;
  }
  .card--front .brand-dot {
    position: absolute;
    left: 50%;
    top: 343px;
    width: 28px;
    height: 28px;
    margin-left: -14px;
    border-radius: 50%;
    background: var(--white);
  }
  .card--front .brand-name {
    position: absolute;
    left: 0; right: 0;
    top: 396px;
  }
  .card--front .tagline {
    position: absolute;
    left: 0; right: 0;
    top: 429px;
    margin: 0;
  }

  .brand-name {
    font-family: "Oswald", sans-serif;
    font-weight: 500;
    font-size: 25px;
    line-height: 1;
    letter-spacing: 0.2px;
  }
  .tagline {
    font-family: "Roboto Condensed", sans-serif;
    font-weight: 700;
    font-size: 8.4px;
    line-height: 1;
    letter-spacing: 2.1px;
    text-transform: uppercase;
    margin-top: 8px;
  }

  /* Back: contact side */
  .card--back {
    left: 617px;
    border-radius: 62px 0 62px 0;
    background: var(--white);
  }
  .card--back .brand-block {
    position: absolute;
    left: 0; right: 0;
    top: 84px;
    text-align: center;
  }
  .card--back .brand-dot {
    width: 32px;
    height: 32px;
    margin: 0 auto 18px;
    border-radius: 50%;
    background: var(--purple);
  }
  .card--back .brand-name { color: var(--purple); }
  .card--back .tagline { color: var(--cyan); }

  .person {
    position: absolute;
    left: 32px;
    top: 307px;
    font-family: "Roboto", sans-serif;
  }
  .person__name {
    color: var(--purple);
    font-weight: 500;
    font-size: 21px;
    line-height: 1;
  }
  .person__title {
    color: var(--cyan);
    font-size: 16px;
    line-height: 1;
    margin-top: 2px;
  }

  .contact-list {
    list-style: none;
    margin-top: 15px;
    font-size: 15.5px;
    color: var(--ink);
  }
  .contact-list li {
    display: flex;
    align-items: center;
    gap: 5px;
    height: 18px;
  }
  .contact-list svg { width: 12px; height: 12px; flex: none; }

  .address {
    font-style: normal;
    margin-top: 14px;
    font-size: 15.5px;
    line-height: 18px;
    color: var(--ink);
  }
</style>
</head>
<body>
<main class="stage">

  <section class="card card--front" aria-label="Card front">
    <div class="backdrop-shape" aria-hidden="true"></div>
    <div class="brand-dot"></div>
    <div class="brand-name">Elvane Behavioral Health</div>
    <div class="tagline">Dedicated to hope, healing and recovery</div>
  </section>

  <section class="card card--back" aria-label="Card back">
    <div class="brand-block">
      <div class="brand-dot"></div>
      <div class="brand-name">Elvane Behavioral Health</div>
      <div class="tagline">Dedicated to hope, healing and recovery</div>
    </div>

    <div class="person">
      <div class="person__name">DANIEL WHITMORE</div>
      <div class="person__title">MANAGING DIRECTOR</div>

      <ul class="contact-list">
        <li>
          <svg viewBox="0 0 24 24" aria-hidden="true"><path fill="var(--purple)" d="M6.6 10.8a15.1 15.1 0 0 0 6.6 6.6l2.2-2.2c.3-.3.7-.4 1-.2 1.1.4 2.3.6 3.6.6.6 0 1 .4 1 1V20c0 .6-.4 1-1 1A17 17 0 0 1 3 4c0-.6.4-1 1-1h3.5c.6 0 1 .4 1 1 0 1.3.2 2.5.6 3.6.1.3 0 .7-.2 1z"/></svg>
          <span>044-987 654 321</span>
        </li>
        <li>
          <svg viewBox="0 0 24 24" aria-hidden="true"><rect x="2" y="5" width="20" height="14" fill="var(--purple)"/><path d="M2 5l10 8 10-8" fill="none" stroke="#fff" stroke-width="1.8"/></svg>
          <span>hello@elvanehealth.com</span>
        </li>
        <li>
          <svg viewBox="0 0 24 24" aria-hidden="true"><g fill="none" stroke="var(--purple)" stroke-width="2"><circle cx="12" cy="12" r="10"/><ellipse cx="12" cy="12" rx="4.5" ry="10"/><path d="M2 12h20M4 7h16M4 17h16"/></g></svg>
          <span>www.elvanehealth.com</span>
        </li>
      </ul>

      <address class="address">
        218, Linden Grove Avenue<br>
        60314,Northbrook County
      </address>
    </div>
  </section>

</main>
</body>
</html>
```